We are a recruitment company based in Norwich/Cambridge England.
I have included our company logo which we want to remain the same.

What we are looking for is a new creative Business card which will really stand out!!

Contact Information for Business Card

Harriet Dunmore
email: Harriet@plavex.co.uk
Address: Brackwell House
Fenmoor Enterprise Park
Partridge Way
Norwich
QB9 3KX
Tel:01632 960418

```html
<!DOCTYPE html>
<html lang="en">
<head>
<meta charset="utf-8">
<title>Plavex Business Card – Harriet Dunmore</title>
<link rel="stylesheet" href="https://fonts.googleapis.com/css2?family=Arimo:wght@700&family=PT+Sans:wght@400&display=swap">
<style>
  :root {
    --brand-green: #8cc63f;
    --brand-grey: #828282;
    --name-grey: #8a8a8c;
    --text-dark: #2f2f2f;
    --card-white: #ffffff;
  }
  * { margin: 0; padding: 0; box-sizing: border-box; }
  html, body {
    width: 1200px;
    height: 686px;
    overflow: hidden;
    background: var(--card-white);
  }
  .card {
    position: relative;
    width: 1200px;
    height: 686px;
    background: var(--card-white);
    font-family: "PT Sans", sans-serif;
    color: var(--text-dark);
    overflow: hidden;
  }
  .card-edges {
    position: absolute;
    inset: 0;
  }
  .brand {
    position: absolute;
    left: 69px;
    top: 97px;
    display: flex;
    align-items: center;
    gap: 16px;
  }
  .brand-dot {
    width: 84px;
    height: 84px;
    border-radius: 50%;
    background: var(--brand-green);
  }
  .brand-name {
    font-family: "PT Sans", sans-serif;
    font-weight: 400;
    font-size: 54px;
    color: var(--brand-grey);
    line-height: 1;
  }
  .holder-name {
    position: absolute;
    right: 71px;
    top: 262px;
    font-family: "Arimo", sans-serif;
    font-weight: 700;
    font-size: 53px;
    letter-spacing: 2px;
    line-height: 1;
    color: var(--name-grey);
    padding-bottom: 6px;
    border-bottom: 5px solid var(--name-grey);
  }
  .contact {
    position: absolute;
    top: 394px;
    display: flex;
    align-items: flex-start;
    gap: 12px;
    font-size: 18.5px;
    line-height: 24px;
  }
  .contact-icon {
    flex: none;
    margin-top: 3px;
  }
  .contact-address { left: 232px; }
  .contact-email { left: 524px; gap: 13px; }
  .contact-phone { left: 816px; gap: 12px; }
  .address-lines { font-style: normal; }
</style>
</head>
<body>
  <main class="card">
    <svg class="card-edges" width="1200" height="686" viewBox="0 0 1200 686" aria-hidden="true">
      <polygon fill="var(--brand-green)" points="0,0 1200,0 1200,41 1111,64 1086,41 0,41"/>
      <polygon fill="var(--brand-green)" points="0,637 78,621 103,643 1095,643 1118,621 1200,637 1200,686 0,686"/>
    </svg>

    <div class="brand">
      <span class="brand-dot"></span>
      <span class="brand-name">Plavex</span>
    </div>

    <h1 class="holder-name">HARRIET DUNMORE</h1>

    <div class="contact contact-address">
      <svg class="contact-icon" width="14" height="19" viewBox="0 0 14 19" aria-hidden="true">
        <path fill="var(--brand-green)" d="M7 0C3.1 0 0 3.1 0 7c0 5 7 12 7 12s7-7 7-12c0-3.9-3.1-7-7-7zm0 9.6A2.6 2.6 0 1 1 7 4.4a2.6 2.6 0 0 1 0 5.2z"/>
      </svg>
      <address class="address-lines">
        Brackwell House<br>
        Fenmoor Enterprise Park<br>
        Partridge Way<br>
        Norwich<br>
        QB9 3KX
      </address>
    </div>

    <div class="contact contact-email">
      <svg class="contact-icon" width="25" height="16" viewBox="0 0 25 16" aria-hidden="true">
        <rect width="25" height="16" fill="var(--brand-green)"/>
        <polyline points="1,1 12.5,9 24,1" fill="none" stroke="var(--card-white)" stroke-width="1.6"/>
        <polyline points="1,15 9.5,7.5 M24,15 15.5,7.5" fill="none" stroke="var(--card-white)" stroke-width="1.2"/>
      </svg>
      <span>Harriet@plavex.co.uk</span>
    </div>

    <div class="contact contact-phone">
      <svg class="contact-icon" width="19" height="19" viewBox="0 0 24 24" aria-hidden="true">
        <path fill="var(--brand-green)" d="M6.6 10.8c1.4 2.8 3.8 5.1 6.6 6.6l2.2-2.2c.3-.3.7-.4 1-.2 1.1.4 2.3.6 3.6.6.6 0 1 .4 1 1V20c0 .6-.4 1-1 1C10.6 21 3 13.4 3 4c0-.6.4-1 1-1h3.5c.6 0 1 .4 1 1 0 1.3.2 2.5.6 3.6.1.3 0 .7-.2 1L6.6 10.8z"/>
      </svg>
      <span>01632 960418</span>
    </div>
  </main>
</body>
</html>
```